Letter design, envelope design, and more

Hello, we the Tavrin Gmbh are looking for our shop. Letter C5. Design does not have to be like a business card, so it can have straight lines. Only the color is important. The logo is the text under TaVRin omit.It should not be playful but Profesionel

Font styles to use
Sans Serif

Colors
0555a3
3176b5
85abd2
85cae6
34a7d8
0792cd
cee9f5
cfdfed
000000

Requirements
Must have
• Color like business card, Please, with the text under TaVRin, Correct address Lindmattstr. 4 Zip code 9517 Goldach, as well as Couvert Without addressing only design and logo with TaVrn
Nice to have
• more writing articles
Should not have
• Not too colored, Text under TaVRin, bright colors

```html
<!DOCTYPE html>
<html lang="en">
<head>
<meta charset="utf-8">
<title>Tavrin Gmbh – Stationery</title>
<link href="https://fonts.googleapis.com/css2?family=Didact+Gothic&family=Roboto:wght@400;700&display=swap" rel="stylesheet">
<style>
  :root{
    --navy:#0b1f5b;
    --bg:#dedede;
    --paper:#f7f7f7;
    --ink:#555a62;
    --ink-soft:#6c717a;
    --rule:#d4d6da;
    --sig:#2f5fb0;
  }
  *{margin:0;padding:0;box-sizing:border-box}
  html,body{width:1200px;height:877px;overflow:hidden;background:var(--bg)}
  .canvas{position:relative;width:1200px;height:877px}

  .wordmark{display:flex;align-items:center;gap:6px;font-family:"Roboto",sans-serif;font-weight:700;color:var(--navy);text-transform:uppercase;letter-spacing:.5px}
  .wordmark .mark{width:14px;height:14px;background:var(--navy)}

  /* Letterhead */
  .letter{position:absolute;left:68px;top:64px;width:528px;height:744px;background:var(--paper);color:var(--ink)}
  .letter .wordmark{position:absolute;left:48px;top:58px;font-size:20px}
  .letter .contact{position:absolute;left:403px;top:40px;padding-left:9px;border-left:1px solid var(--rule);height:62px;font-family:"Roboto",sans-serif;font-size:7.6px;line-height:10px;color:var(--ink)}
  .contact .addr{margin-bottom:4px}
  .contact .line{display:flex;align-items:center;gap:4px}
  .contact svg{width:7px;height:7px;fill:var(--navy)}
  .letter .salutation{position:absolute;left:46px;top:206px;font-family:"Didact Gothic",sans-serif;font-size:14px;color:var(--ink)}
  .letter .body{position:absolute;left:46px;top:247px;width:440px;font-family:"Didact Gothic",sans-serif;font-size:7.6px;line-height:11.4px;text-align:justify;color:var(--ink-soft)}
  .body p{margin-bottom:11.4px}
  .letter .closing{position:absolute;left:46px;top:487px;font-family:"Didact Gothic",sans-serif;font-size:7.6px;color:var(--ink-soft)}
  .letter .signature{position:absolute;left:42px;top:518px;width:94px;height:38px;background:linear-gradient(90deg,rgba(47,95,176,.18),rgba(47,95,176,.06))}
  .letter-band{position:absolute;left:66px;top:798px;width:530px;height:10px;background:var(--navy);border-top:1px solid #fff}

  /* Envelope back */
  .envelope-back{position:absolute;left:614px;top:269px;width:530px;height:240px;background:var(--paper)}
  .envelope-back svg{position:absolute;left:0;top:0}
  .envelope-back .flap-name{position:absolute;left:0;top:30px;width:530px;text-align:center;font-family:"Roboto",sans-serif;font-weight:700;font-size:15px;letter-spacing:1px;color:#fff;text-transform:uppercase}

  /* Envelope front */
  .envelope-front{position:absolute;left:614px;top:562px;width:533px;height:244px;background:var(--paper)}
  .envelope-front .wordmark{position:absolute;left:28px;top:30px;font-size:17px}
  .envelope-front .return{position:absolute;left:28px;top:70px;font-family:"Roboto",sans-serif;font-size:7px;color:var(--ink)}
  .envelope-front .band{position:absolute;left:0;bottom:0;width:533px;height:10px;background:var(--navy);border-top:1px solid #fff}
</style>
</head>
<body>
<div class="canvas">

  <section class="letter">
    <div class="wordmark"><span class="mark"></span>Tavrin Gmbh</div>
    <div class="contact">
      <div class="addr">Lindmattstr. 4<br>9517 Goldach</div>
      <div class="line"><svg viewBox="0 0 10 10"><path d="M2 0l2 2-1 2c1 2 2 3 3 3l1-1 3 2-1 2C4 10 0 6 0 2z"/></svg>+41 71 555 04 20</div>
      <div class="line"><svg viewBox="0 0 10 10"><path d="M0 2h10v6H0z M0 2l5 3 5-3" stroke="#fff" stroke-width=".8"/></svg>info@tavrin.ch</div>
      <div class="line"><svg viewBox="0 0 10 10"><circle cx="5" cy="5" r="5"/></svg>www.tavrin.ch</div>
    </div>

    <div class="salutation">Dear Mr. Keller,</div>
    <div class="body">
      <p>Lorem ipsum dolor sit amet, consectetur adipiscing elit. Donec orci purus, luctus vitae dignissim eu, iaculis sed purus. Vivamus faucibus, ipsum nec aliquet viverra, leo mauris condimentum ligula, sit amet sagittis enim ligula quis arcu. Nam egestas tortor id nisi porttitor mattis. In tortor ante, ultricies in suscipit a, tempus non massa. Vivamus et auctor mi. Fusce vel massa nulla. Phasellus nec eros mauris, et scelerisque orci.</p>
      <p>Donec malesuada orci vitae nulla accumsan porta a id massa. Quisque accumsan iaculis magna sit amet fringilla. Maecenas consequat, magna eget tincidunt semper, odio nibh rutrum mi, id feugiat ante nisi eu risus. Vestibulum nunc orci, rhoncus a placerat in, ultricies in mi. Cras mattis varius eros, vel fringilla nisi suscipit eget. Quisque scelerisque sagittis nulla at porttitor.</p>
      <p>Sed id augue vitae urna euismod commodo aliquet a quam. Pellentesque arcu velit, cursus et malesuada ut, consequat et diam. Nullam erat sem, rhoncus id ullamcorper vitae, rhoncus et arcu. In ultricies ultricies nulla, ut rutrum nisi iaculis at. Donec eu magna a metus ornare faucibus. Fusce aliquet faucibus ultricies. Morbi semper, est id tincidunt gravida, sem arcu adipiscing lacus, ac bibendum nulla leo eu purus. Quisque nec diam sed risus consectetur a ccumsan quis quis nibh. Vestibulum id purus lorem.</p>
      <p>It is a long established fact that a reader will be distracted by the readable content of a page when looking at its layout. The point of using Lorem Ipsum is that it has a more-or-less normal distribution of letters, as opposed to using 'Content here, content here', making it look like readable English. Many desktop publishing packages</p>
    </div>
    <div class="closing">Sincerely,</div>
    <div class="signature" role="img" aria-label="Handwritten signature of Jonas Keller"></div>
  </section>
  <div class="letter-band"></div>

  <section class="envelope-back">
    <svg width="530" height="76" viewBox="0 0 530 76" aria-hidden="true">
      <path d="M0 0H530L524 26Q516 74 480 74H50Q14 74 7 26Z" fill="var(--navy)"/>
    </svg>
    <div class="flap-name">Tavrin</div>
  </section>

  <section class="envelope-front">
    <div class="wordmark"><span class="mark"></span>Tavrin Gmbh</div>
    <div class="return">Lindmattstr. 4, 9517 Goldach</div>
    <div class="band"></div>
  </section>

</div>
</body>
</html>
```